Tandem Hearth Works Pty Ltd

We need business cards for a company based in Perth, we install, service and maintain fire equipment.
On the front we want a great design with our logo and a small spot for our full company name, general company email address and office number. On the back we need space for our name, title, mobile number and email address on the back.

Target Market(s)

Facility managers and commercial/industrial building owners/occupiers.

Contact Information for Business Card

Font styles to use
Sans Serif

Requirements
Must have
• Please only submit 5 of your best samples.
Darker tones are preferred.
Nice to have
• We want to use, black, red and grey. Keep it modern and clean.
I've attached the company logo and a sample of a boarder we use on our emergency plans.
Should not have
• No preference. Let the designer choose.

```html
<!DOCTYPE html>
<html lang="en">
<head>
<meta charset="utf-8">
<title>Tandem Hearth Works – Business Cards</title>
<link rel="stylesheet" href="https://fonts.googleapis.com/css2?family=Fira+Sans:wght@300;400;600;700&display=swap">
<style>
  :root {
    --canvas: #dfe7dc;
    --ink: #000000;
    --paper: #ffffff;
    --brand-red: #ee2430;
    --flame-deep: #e8452a;
    --flame-mid: #f48a22;
    --flame-light: #fcc016;
    --font-main: "Fira Sans", Arial, sans-serif;
  }
  * { box-sizing: border-box; margin: 0; padding: 0; }
  html, body {
    width: 1200px; height: 1200px; overflow: hidden;
    background: var(--canvas);
    font-family: var(--font-main);
  }
  .sheet { position: relative; width: 1200px; height: 1200px; }
  .card {
    position: absolute; left: 246px; width: 711px; height: 406px; overflow: hidden;
  }

  /* Front */
  .card-front { top: 148px; background: var(--ink); color: var(--paper); }
  .company-name {
    position: absolute; left: 45px; top: 42px;
    font-size: 30px; font-weight: 600; color: var(--brand-red); letter-spacing: 0.2px;
  }
  .office-details {
    position: absolute; left: 45px; top: 98px;
    font-size: 23px; font-weight: 300; line-height: 25.5px;
  }
  .flame-art {
    position: absolute; left: 412px; top: 14px; width: 265px; height: 392px;
    border-radius: 50% 50% 0 0 / 70% 70% 0 0;
    background: linear-gradient(to top, var(--flame-deep) 0%, var(--flame-mid) 55%, var(--flame-light) 85%, rgba(252,192,22,0) 100%);
  }
  .brand-mark {
    position: absolute; left: 458px; top: 296px;
    font-size: 86px; font-weight: 700; line-height: 1; color: var(--paper); letter-spacing: -1px;
  }

  /* Back */
  .card-back { top: 652px; height: 403px; background: var(--paper); color: var(--ink); }
  .person {
    position: absolute; right: 40px; top: 42px; text-align: right;
  }
  .person-name { font-size: 32px; font-weight: 300; line-height: 1; letter-spacing: 0.5px; }
  .person-name strong { font-weight: 700; }
  .person-title { font-size: 23px; font-weight: 300; margin-top: 6px; }
  .contact-panel {
    position: absolute; left: 0; top: 184px; width: 453px; height: 146px;
    background: var(--brand-red); color: var(--paper);
    border-radius: 0 34px 34px 0;
    padding: 30px 0 0 33px;
  }
  .contact-list { list-style: none; }
  .contact-item {
    display: flex; align-items: center; gap: 11px;
    font-size: 23px; font-weight: 300; height: 28px; margin-bottom: 0;
  }
  .contact-icon { width: 23px; height: 23px; flex: none; }
  .base-band {
    position: absolute; left: 0; bottom: 0; width: 100%; height: 22px; background: var(--ink);
  }
</style>
</head>
<body>
<main class="sheet">
  <section class="card card-front" aria-label="Card front">
    <h1 class="company-name">Tandem Hearth Works Pty Ltd</h1>
    <p class="office-details">
      123 Street Name, State,<br>
      Country Pincode.<br>
      Ph: +000 12345678<br>
      email@hostname.com
    </p>
    <div class="flame-art" role="img" aria-label="Illustration of rising orange and yellow flames"></div>
    <div class="brand-mark">THW</div>
  </section>

  <section class="card card-back" aria-label="Card back">
    <div class="person">
      <p class="person-name">FIRST <strong>NAME</strong></p>
      <p class="person-title">Designation</p>
    </div>
    <div class="contact-panel">
      <ul class="contact-list">
        <li class="contact-item">
          <svg class="contact-icon" viewBox="0 0 24 24" aria-hidden="true">
            <circle cx="12" cy="12" r="12" fill="#fff"/>
            <path d="M12 5 L19 11.5 H17 V18 H13.5 V14 H10.5 V18 H7 V11.5 H5 Z" fill="#ee2430"/>
          </svg>
          <span>123 Street Name, Country Pincode.</span>
        </li>
        <li class="contact-item">
          <svg class="contact-icon" viewBox="0 0 24 24" aria-hidden="true">
            <circle cx="12" cy="12" r="12" fill="#fff"/>
            <rect x="8" y="5" width="8" height="14" rx="1.5" fill="#ee2430"/>
            <rect x="9.5" y="7" width="5" height="5" fill="#fff"/>
          </svg>
          <span>Ph: +000 12345678</span>
        </li>
        <li class="contact-item">
          <svg class="contact-icon" viewBox="0 0 24 24" aria-hidden="true">
            <circle cx="12" cy="12" r="12" fill="#fff"/>
            <rect x="5.5" y="7.5" width="13" height="9" fill="none" stroke="#ee2430" stroke-width="1.6"/>
            <path d="M5.5 7.5 L12 13 L18.5 7.5 M5.5 16.5 L10 12 M18.5 16.5 L14 12" fill="none" stroke="#ee2430" stroke-width="1.4"/>
          </svg>
          <span>email@hostname.com</span>
        </li>
      </ul>
    </div>
    <div class="base-band"></div>
  </section>
</main>
</body>
</html>
```